Business cards for a fun web development agency

Hi,I am building a web development agency. You can read about it on the website http://kite-loft.examplehost.com. Basically, I want to focus on free and open source products and stay as far away from the corporate business feeling as possible. I want to build a community so I want the business card to feel fun and approachable (at the risk of professional if need be). I am uploading some of my image assets in various file formats. Feel free to use them or make your own if you want just keeping in theme with the website.
Industry/Entity Type
Building
Contact Information for Business Card
Company Name: Boat ShedWebsite: www.kiteloftdev.example (it's currently in alpha on http://kite-loft.examplehost.com if you want to see the them we are trying to capture)My name is: Banner B. SchaferMy email: banner@boatsheddev.comMy phone: 0431 587 904
Look and feel

```html
<!DOCTYPE html>
<html lang="en">
<head>
<meta charset="utf-8">
<title>Kite Loft — Business Cards</title>
<link rel="stylesheet" href="https://fonts.googleapis.com/css2?family=Questrial&family=Open+Sans:wght@700&display=swap">
<style>
  :root {
    --backdrop: #e8e5e1;
    --card-white: #ffffff;
    --band-blue: #1783b4;
    --slate: #43658b;
    --logo-navy: #3b5478;
    --text-light: #ffffff;
  }
  html, body {
    margin: 0;
    width: 1200px;
    height: 1000px;
    overflow: hidden;
    background: var(--backdrop);
  }
  .canvas {
    position: relative;
    width: 1200px;
    height: 1000px;
  }
  .card {
    position: absolute;
    left: 265px;
    width: 666px;
    box-shadow: 0 4px 14px rgba(0,0,0,0.18);
  }
  .card--front {
    top: 73px;
    height: 397px;
    background: var(--card-white);
  }
  .card--back {
    top: 533px;
    height: 396px;
    background: var(--slate);
  }
  .wordmark {
    position: absolute;
    left: 0;
    right: 0;
    text-align: center;
    font-family: "Questrial", sans-serif;
    font-size: 60px;
    letter-spacing: 1px;
    line-height: 1;
    white-space: nowrap;
  }
  .card--front .wordmark { top: 84px; color: var(--logo-navy); }
  .card--back .wordmark { top: 170px; color: var(--text-light); }

  .side-bar {
    position: absolute;
    top: 213px;
    width: 22px;
    height: 143px;
    background: var(--slate);
  }
  .side-bar--left { left: 0; }
  .side-bar--right { right: 0; }
  .contact-band {
    position: absolute;
    top: 213px;
    left: 28px;
    width: 610px;
    height: 143px;
    background: var(--band-blue);
    color: var(--text-light);
  }
  .holder-name {
    position: absolute;
    left: 54px;
    top: 58px;
    font-family: "Open Sans", sans-serif;
    font-weight: 700;
    font-size: 19px;
  }
  .contact-list {
    position: absolute;
    left: 326px;
    top: 38px;
    margin: 0;
    padding: 0;
    list-style: none;
    font-family: "Questrial", sans-serif;
    font-size: 17px;
    line-height: 21.5px;
  }
  .contact-list li {
    display: flex;
    align-items: center;
    gap: 6px;
  }
  .contact-list svg { width: 13px; height: 13px; flex: none; }
  .back-url {
    position: absolute;
    left: 0;
    right: 0;
    top: 335px;
    text-align: center;
    font-family: "Questrial", sans-serif;
    font-size: 17px;
    color: var(--text-light);
  }
</style>
</head>
<body>
<main class="canvas">
  <section class="card card--front">
    <div class="wordmark">KITE LOFT</div>
    <div class="side-bar side-bar--left"></div>
    <div class="contact-band">
      <div class="holder-name">Corwin T. Aldous</div>
      <ul class="contact-list">
        <li>
          <svg viewBox="0 0 16 16" aria-hidden="true"><path d="M4 1.5c.6 0 2 2.6 2 3.2 0 .6-1.2 1.2-1.1 1.7.3 1.6 2.8 4.2 4.5 4.6.5.1 1.1-1.1 1.7-1.1.6 0 3.2 1.4 3.2 2 0 1-1.4 2.6-2.6 2.6C7 14.5 1.5 9 1.5 4.1 1.5 2.9 3 1.5 4 1.5z" fill="#fff"/></svg>
          0431 587 904
        </li>
        <li>
          <svg viewBox="0 0 16 16" aria-hidden="true"><rect x="1" y="3" width="14" height="10" fill="#fff"/><path d="M1.5 3.5 8 9l6.5-5.5" stroke="#1783b4" stroke-width="1.4" fill="none"/></svg>
          corwin@kiteloftdev.example
        </li>
        <li>
          <svg viewBox="0 0 16 16" aria-hidden="true"><g fill="none" stroke="#fff" stroke-width="1.3"><circle cx="8" cy="8" r="6.3"/><ellipse cx="8" cy="8" rx="2.8" ry="6.3"/><path d="M1.7 8h12.6M2.8 4.8h10.4M2.8 11.2h10.4"/></g></svg>
          www.kiteloftdev.example
        </li>
      </ul>
    </div>
    <div class="side-bar side-bar--right"></div>
  </section>

  <section class="card card--back">
    <div class="wordmark">KITE LOFT</div>
    <div class="back-url">www.kiteloftdev.example</div>
  </section>
</main>
</body>
</html>
```